Mortgage Protection Insurance Flyer

The target audience are new home owners so the design needs to be clean and simple.

This a primarily for Final Expense Insurance, but need an area where it says "We Also Specialize In:"
- Medicare Supplement Insurance (MediGap)
- Annuities
- Final Expense

All flyer versions need to be editable. Colors to be used are red, white or black. Refer to my website for colors and photos (corvantshield.com). Will attach my logo and a flyer that I found online that is the format that I am looking for (for 8.5 in. x 11 in version). Need flyer in standard letter size 8.5 in. x11 in. but also in 8.5 in. x 5.5 in and 5.0 in. x 8.0 in. All sizes to be portrait oriented. If picked as winning design, need all flyer versions in full color, also in grey scale and files in all industry file types.

Content can be taken from my website..... corvantshield.com

Do NOT submit if you are not willing to provide all versions as described above for the original project price.

Must use royalty-free stock photos please.

Target Market(s)

New homeowners looking for insurance to protect there mortgage payments

Industry/Entity Type

Life Insurance

Colors
f69fa3

Requirements
Must have
• Colors to be used are red, white or black.
• Need flyer in standard letter size 8.5 in. x11 in. but also in 3.5 in. x 8.5 in (Full Bleed 3.75 in by 8.75 in.) and 4.0 in. x 6.0 in. (Full Bleed 4.12 in x 6.12 in) Each design tailored to the size dimensions (So no squeezing 8.5 x 11 design into a 4.0 x 6.0 space.) All sizes to be portrait oriented. If picked as winning design, need all flyer versions in full color, also in grey scale and files in all file types.
• Do not need physical address on flyer, do need email address on flyer though - tkelwer@corvantshield.com
• So phone number should be prominent, email address and website address should also be contact area.
• If you can not agree to terms above, do not submit any designs.
• Need facebook & twitter logos somewhere in contact info area.
Nice to have
• See sample flyers I have attached.
• White background with red used as primary graphic color and black used as secondary graphic if needed.
• font to be used should similar to one used in logo.

```html
<!DOCTYPE html>
<html lang="en">
<head>
<meta charset="utf-8">
<title>Mortgage Protection Rack Card 3.5x8.5</title>
<link href="https://fonts.googleapis.com/css2?family=Anton&family=Lato:wght@400;700;900&family=Montserrat:wght@300&family=Rubik:wght@700;800&display=swap" rel="stylesheet">
<style>
  :root{
    --board:#d8d8d8;
    --ink:#1d1d1d;
    --paper:#ffffff;
    --body:#2a2a2a;
    --title:#5a5a5a;
  }
  *{box-sizing:border-box;margin:0;padding:0}
  html,body{width:1200px;height:1200px;overflow:hidden;background:var(--board)}
  .board{position:relative;width:1200px;height:1200px}
  .board-title{position:absolute;top:94px;left:0;width:1160px;text-align:center;
    font:300 39px/1 "Montserrat",sans-serif;color:var(--title);letter-spacing:.5px}

  .flyer{
    --accent:#e10b12;
    --accent-dark:#a2151a;
    --heading:#c8161d;
    --photo-a:#f4f4f5;
    --photo-b:#d9d4cf;
    --box-a:#f01b1b;
    --box-b:#c9141a;
    --foot-a:#e01017;
    --foot-b:#8e1a1f;
    position:absolute;top:205px;width:378px;height:882px;background:var(--paper);overflow:hidden;
    font-family:"Lato",sans-serif;color:var(--body)
  }
  .flyer--color{left:167px}
  .flyer--mono{left:655px;
    --accent:#6a6a6a;--accent-dark:#444;--heading:#5c5c5c;
    --photo-a:#f3f3f3;--photo-b:#cfcfcf;
    --box-a:#7a7a7a;--box-b:#555;
    --foot-a:#6f6f6f;--foot-b:#3c3c3c}

  .hero{position:absolute;inset:0 0 auto 0;height:335px}
  .hero-photo{position:absolute;inset:0;background:linear-gradient(120deg,var(--photo-a) 30%,var(--photo-b) 100%)}
  .hero-shapes{position:absolute;inset:0}
  .fill-paper{fill:var(--paper)}
  .line-ink{fill:none;stroke:var(--ink)}
  .line-accent{fill:none;stroke:var(--accent)}

  .brand{position:absolute;left:29px;top:38px;font:800 18px/1 "Rubik",sans-serif;color:var(--ink);letter-spacing:.5px}

  .headline{position:absolute;left:28px;top:166px;font-family:"Anton",sans-serif;line-height:1;text-transform:uppercase}
  .headline .h-our{display:block;font-size:37px;color:var(--ink)}
  .headline .h-plans{display:block;font-size:35px;color:var(--accent);margin-top:4px}
  .headline .h-based{display:block;font-size:21.5px;color:var(--ink);margin-top:6px}

  .intro{position:absolute;left:31px;top:346px;width:130px}
  .section-title{font:700 12px/1.05 "Rubik",sans-serif;color:var(--heading);letter-spacing:.3px}
  .intro p{font-size:8.4px;line-height:1.28;text-align:justify;margin-top:10px}
  .intro p + p{margin-top:10px}

  .benefits{position:absolute;left:186px;top:341px;width:169px;height:216px;border-radius:12px;
    background:linear-gradient(180deg,var(--box-a),var(--box-b));color:#fff;padding:42px 10px 0 10px}
  .benefits-tag{position:absolute;left:-8px;top:17px;width:70px;height:14px;border-radius:0 8px 8px 0;
    background:#3a3a3a;font:700 8px/14px "Lato",sans-serif;color:#fff;padding-left:17px}
  .benefits-tag::before{content:"";position:absolute;left:0;top:14px;border-top:5px solid #1a1a1a;border-left:8px solid transparent}
  .benefits ul{list-style:none}
  .benefits li{position:relative;padding-left:12px;font:700 7.6px/1.3 "Lato",sans-serif;margin-bottom:12px}

  .tick{position:absolute;left:0;top:1px;width:8px;height:8px;border:1px solid currentColor;border-radius:50%}
  .tick::after{content:"";position:absolute;left:2px;top:1px;width:2px;height:3.5px;border:solid currentColor;border-width:0 1px 1px 0;transform:rotate(40deg)}

  .story{position:absolute;left:31px;top:593px;width:310px;font-size:8.4px;line-height:1.3}
  .story p + p{margin-top:12px}

  .specialties{position:absolute;left:31px;top:701px;width:320px}
  .specialties .section-title{font-size:12px}
  .spec-list{list-style:none;position:relative;margin-top:11px;height:30px;font-size:8.4px}
  .spec-list li{position:absolute;padding-left:14px;color:var(--body)}
  .spec-list .tick{color:var(--accent)}
  .spec-medigap{left:0;top:0}
  .spec-final{left:0;top:15px}
  .spec-annuities{left:208px;top:1px;padding-left:21px!important}

  .footer{position:absolute;left:0;top:750px;width:378px;height:132px}
  .call{position:absolute;left:26px;top:808px;color:#fff;font-family:"Lato",sans-serif}
  .call-label{font-weight:700;font-size:11.5px}
  .call-number{font-weight:900;font-size:18.5px;margin-top:2px;letter-spacing:.2px}
  .contacts{position:absolute;left:176px;top:807px;list-style:none;color:#fff}
  .contacts li{display:flex;align-items:center;height:20px;margin-bottom:4px;font:700 7px/1 "Lato",sans-serif}
  .contact-icon{width:19px;height:19px;border:1px solid #fff;border-radius:50%;margin-right:6px;flex:none}
  .social{position:absolute;left:299px;top:849px;display:flex;gap:2px}
  .social span{width:9px;height:9px;background:#fff;border-radius:1px}
</style>
</head>
<body>
<div class="board">
  <h1 class="board-title">Mortgage Protection_3.5x8.5</h1>

  <!-- Full colour version -->
  <article class="flyer flyer--color">
    <div class="hero">
      <div class="hero-photo" role="img" aria-label="Photo of a smiling senior couple embracing"></div>
      <svg class="hero-shapes" viewBox="0 0 378 335" width="378" height="335" aria-hidden="true">
        <path class="fill-paper" d="M0 0 H262 C200 70 100 105 0 112 Z"/>
        <path class="line-accent" stroke-width="3" d="M270 0 C206 78 104 114 0 118"/>
        <path class="line-ink" stroke-width="5" d="M262 0 C200 70 100 105 0 112"/>
        <path class="fill-paper" d="M0 314 Q50 332 150 324 Q270 312 378 282 V335 H0 Z"/>
        <path class="line-ink" stroke-width="6" d="M0 298 Q45 318 140 313 Q265 302 378 271"/>
        <path class="line-accent" stroke-width="2.5" d="M0 314 Q50 332 150 324 Q270 312 378 282"/>
      </svg>
    </div>
    <div class="brand">CORVANT SHIELD</div>
    <h2 class="headline"><span class="h-our">Our</span><span class="h-plans">Plans Are</span><span class="h-based">Based on Yours</span></h2>

    <section class="intro">
      <h3 class="section-title">Mortgage Protection Insurance</h3>
      <p>Mortgage Protection Insurance (MPI) is a type of decreasing term life insurance policy designed to pay off your mortgage if you were to pass away — and many policies also cover mortgage payments (usually for a limited period of time) if you become disabled.</p>
      <p>Unforeseen events and a lack of the right kind of insurance can spell trouble quickly. Contact us today, to set up a free assessment time. We will analyze your insurance needs and get you and your family the right coverage quickly at a budget friendly price.</p>
    </section>

    <section class="benefits">
      <div class="benefits-tag">Benefits:</div>
      <ul>
        <li><span class="tick"></span>Guaranteed approval. Even if you're in poor health or work in a dangerous profession, there is guaranteed approval with no medical exams or lab tests.</li>
        <li><span class="tick"></span>No guesswork. The check goes straight to the lender for the exact mortgage balance, so there'll always be enough and your family won't have to handle the money.</li>
        <li><span class="tick"></span>Disability protection. Many MPI policies make mortgage payments (usually for a limited time) if you become disabled or lose your job.</li>
      </ul>
    </section>

    <section class="story">
      <p>We have been helping clients in Northern Idaho/Eastern Washington prepare for the unknown.</p>
      <p>We have access to the industry's top insurance carriers so you can get the right coverage, that fits your budget.</p>
      <p>Find out how we can give you the peace of mind of knowing your family will not have a financial burden if something were to happen to you.</p>
    </section>

    <section class="specialties">
      <h3 class="section-title">We Also Specialize In:</h3>
      <ul class="spec-list">
        <li class="spec-medigap"><span class="tick"></span>Medicare Supplement Insurance (Medigap)</li>
        <li class="spec-final"><span class="tick"></span>Final Expense Insurance</li>
        <li class="spec-annuities"><span class="tick"></span>Annuities</li>
      </ul>
    </section>

    <svg class="footer" viewBox="0 0 378 132" width="378" height="132" aria-hidden="true">
      <defs>
        <linearGradient id="footColor" x1="0" y1="0" x2="0" y2="1">
          <stop offset="0" stop-color="#e01017"/><stop offset="1" stop-color="#8e1a1f"/>
        </linearGradient>
      </defs>
      <path fill="url(#footColor)" d="M0 36 Q110 16 220 26 Q320 34 378 8 V132 H0 Z"/>
      <path class="line-ink" stroke-width="5" d="M0 26 Q110 6 220 17 Q320 25 378 0"/>
    </svg>
    <div class="call"><div class="call-label">Call us now:</div><div class="call-number">(555)410.2378</div></div>
    <ul class="contacts">
      <li><span class="contact-icon"></span>tkelwer@corvantshield.com</li>
      <li><span class="contact-icon"></span>corvantshield.com</li>
    </ul>
    <div class="social"><span></span><span></span></div>
  </article>

  <!-- Greyscale version -->
  <article class="flyer flyer--mono">
    <div class="hero">
      <div class="hero-photo" role="img" aria-label="Greyscale photo of a smiling senior couple embracing"></div>
      <svg class="hero-shapes" viewBox="0 0 378 335" width="378" height="335" aria-hidden="true">
        <path class="fill-paper" d="M0 0 H262 C200 70 100 105 0 112 Z"/>
        <path class="line-accent" stroke-width="3" d="M270 0 C206 78 104 114 0 118"/>
        <path class="line-ink" stroke-width="5" d="M262 0 C200 70 100 105 0 112"/>
        <path class="fill-paper" d="M0 314 Q50 332 150 324 Q270 312 378 282 V335 H0 Z"/>
        <path class="line-ink" stroke-width="6" d="M0 298 Q45 318 140 313 Q265 302 378 271"/>
        <path class="line-accent" stroke-width="2.5" d="M0 314 Q50 332 150 324 Q270 312 378 282"/>
      </svg>
    </div>
    <div class="brand">CORVANT SHIELD</div>
    <h2 class="headline"><span class="h-our">Our</span><span class="h-plans">Plans Are</span><span class="h-based">Based on Yours</span></h2>

    <section class="intro">
      <h3 class="section-title">Mortgage Protection Insurance</h3>
      <p>Mortgage Protection Insurance (MPI) is a type of decreasing term life insurance policy designed to pay off your mortgage if you were to pass away — and many policies also cover mortgage payments (usually for a limited period of time) if you become disabled.</p>
      <p>Unforeseen events and a lack of the right kind of insurance can spell trouble quickly. Contact us today, to set up a free assessment time. We will analyze your insurance needs and get you and your family the right coverage quickly at a budget friendly price.</p>
    </section>

    <section class="benefits">
      <div class="benefits-tag">Benefits:</div>
      <ul>
        <li><span class="tick"></span>Guaranteed approval. Even if you're in poor health or work in a dangerous profession, there is guaranteed approval with no medical exams or lab tests.</li>
        <li><span class="tick"></span>No guesswork. The check goes straight to the lender for the exact mortgage balance, so there'll always be enough and your family won't have to handle the money.</li>
        <li><span class="tick"></span>Disability protection. Many MPI policies make mortgage payments (usually for a limited time) if you become disabled or lose your job.</li>
      </ul>
    </section>

    <section class="story">
      <p>We have been helping clients in Northern Idaho/Eastern Washington prepare for the unknown.</p>
      <p>We have access to the industry's top insurance carriers so you can get the right coverage, that fits your budget.</p>
      <p>Find out how we can give you the peace of mind of knowing your family will not have a financial burden if something were to happen to you.</p>
    </section>

    <section class="specialties">
      <h3 class="section-title">We Also Specialize In:</h3>
      <ul class="spec-list">
        <li class="spec-medigap"><span class="tick"></span>Medicare Supplement Insurance (Medigap)</li>
        <li class="spec-final"><span class="tick"></span>Final Expense Insurance</li>
        <li class="spec-annuities"><span class="tick"></span>Annuities</li>
      </ul>
    </section>

    <svg class="footer" viewBox="0 0 378 132" width="378" height="132" aria-hidden="true">
      <defs>
        <linearGradient id="footMono" x1="0" y1="0" x2="0" y2="1">
          <stop offset="0" stop-color="#6f6f6f"/><stop offset="1" stop-color="#3c3c3c"/>
        </linearGradient>
      </defs>
      <path fill="url(#footMono)" d="M0 36 Q110 16 220 26 Q320 34 378 8 V132 H0 Z"/>
      <path class="line-ink" stroke-width="5" d="M0 26 Q110 6 220 17 Q320 25 378 0"/>
    </svg>
    <div class="call"><div class="call-label">Call us now:</div><div class="call-number">(555)410.2378</div></div>
    <ul class="contacts">
      <li><span class="contact-icon"></span>tkelwer@corvantshield.com</li>
      <li><span class="contact-icon"></span>corvantshield.com</li>
    </ul>
    <div class="social"><span></span><span></span></div>
  </article>
</div>
</body>
</html>
```